Flyer für Backwarenlieferservice
Liebe Designer,
wir sind begeistert, dass du die Möglichkeit hast, das Design für unseren Werbeflyer zu gestalten. Unser Backwarenlieferservice, die 'Teigwichtelhof', legt großen Wert auf eine kreative und ansprechende Gestaltung, die unsere Probessendung in den Mittelpunkt stellt. Bitte beachte die folgenden Informationen bei der Entwicklung deines Designs:
WICHTIG FÜR UNS: Das unser Maskottchen eingebunden ist und das wir mit dem Flyer für unsere kostenlose Probesendung in den Fokus stellen wollen. Ein altes Design ist im Anhang, der Text sollte nicht identisch sein, aber in die Richtung gehen.
Aufgabenstellung
1. Was ist uns besonders wichtig im Design?
Einladende Optik: Das Design sollte fröhlich und einladend wirken, um die Freude an köstlichen Backwaren zu betonen.
Fokussierung auf die Probessendung: Betone die Möglichkeit, unsere Backwaren einmalig kostenlos auszuprobieren. Dies sollte klar und auffällig im Design integriert sein.
Kinderfreundlichkeit: Da junge Familien eine wichtige Zielgruppe sind, ist ein kinderfreundliches Design mit ansprechenden Illustrationen oder Bildern von Backwaren für Kinder wünschenswert.
Klare und prägnante Botschaft: Die Botschaft sollte leicht verständlich und einprägsam sein, damit potenzielle Kunden sofort die Vorteile unserer Probessendung erkennen.
2. Was macht unsere Firma aus?
Probessendung: Unser Alleinstellungsmerkmal ist die kostenlose Probessendung, die es neuen Kunden ermöglicht, unsere Backwaren unverbindlich zu testen.
Qualität und Vielfalt: Betone die Qualität und Vielfalt unserer Backwaren. Bilder von handwerklich hergestellten, knusprigen Produkten können dabei hilfreich sein.
Familienfreundlichkeit: Wir sind darauf ausgerichtet, auch den Bedürfnissen von jungen Familien gerecht zu werden. Dies spiegelt sich in unserem Sortiment und unseren Angeboten wider.
3. Wer ist unsere Zielgruppe?
Junge Familien mit Kindern: Eltern, die nach hochwertigen Backwaren suchen und Wert auf eine kostenlose Probessendung legen, um unser Sortiment kennenzulernen.
Alle Personen ab ca. 25 Jahren: Auch Einzelpersonen und Paare ab 25 Jahren, die auf der Suche nach qualitativ hochwertigen und abwechslungsreichen Backwaren sind.
Designelemente:
Schriften: Nutze die Schriften 'Audiowide' und 'Alike' für einen einheitlichen Markenauftritt.
Farben: Unsere Hauptfarben sind Grau und Orange. Bitte integriere diese Farben harmonisch in das Design.
Format: Der Flyer hat das A5-Format, aber auch andere Formate können in Betracht gezogen werden.
Vielen Dank für deine Kreati..

```html
<!DOCTYPE html>
<html lang="de">
<head>
<meta charset="utf-8">
<title>Teigwichtelhof – Flyer Vorder- und Rückseite</title>
<link href="https://fonts.googleapis.com/css2?family=Alike&family=Audiowide&display=swap" rel="stylesheet">
<style>
:root{
  --orange:#e8822a;
  --orange-light:#f2a03a;
  --dark:#2a2a2a;
  --darker:#1e1b19;
  --peach:#f3d4ae;
  --tan:#c9a27a;
  --white:#ffffff;
  --text:#2b2b2b;
  --stage:#9a9a9a;
}
*{margin:0;padding:0;box-sizing:border-box}
html,body{width:1200px;height:1117px;overflow:hidden}
body{background:var(--stage);position:relative;font-family:'Alike',serif;color:var(--text)}
.page{position:absolute;top:188px;width:522px;height:741px;overflow:hidden;background:var(--dark)}
.page--front{left:64px}
.page--back{left:612px}
.page svg.layer{position:absolute;inset:0;width:100%;height:100%}
.abs{position:absolute}
.brand-name{font-family:'Audiowide',sans-serif;color:var(--orange);font-size:15px;letter-spacing:6px;left:0;right:0;top:138px;text-align:center}
.ribbon-kicker{font-family:'Audiowide',sans-serif;color:var(--white);font-size:17px;left:0;right:0;top:188px;text-align:center}
.ribbon-main{font-family:'Audiowide',sans-serif;color:var(--white);font-size:57px;line-height:1;left:0;right:0;top:210px;text-align:center;text-shadow:1px 2px 2px rgba(0,0,0,.25)}
.ribbon-sub{font-family:'Audiowide',sans-serif;color:var(--white);font-size:33px;line-height:1;left:0;right:0;top:269px;text-align:center}
.intro-head{left:60px;right:60px;top:333px;text-align:center;font-size:14.2px;line-height:15.8px;color:var(--text)}
.intro-body{left:54px;right:54px;top:374px;text-align:center;font-size:10.4px;line-height:11.9px;color:#3a3a3a}
.usp{position:absolute;top:454px;height:32px;border:2px solid var(--orange);border-radius:3px;background:var(--white);display:flex;align-items:center;justify-content:center;font-size:14px;color:var(--text)}
.usp--one{left:42px;width:152px}
.usp--two{left:203px;width:280px}
.url{font-family:'Alike',serif;color:var(--white);font-size:17px;text-align:center}
.card-title{font-family:'Audiowide',sans-serif;color:var(--orange);font-size:14.5px;line-height:16px}
.card-text{font-size:11px;line-height:12.6px;color:var(--text)}
.card-text--small{font-size:9.7px;line-height:11.2px}
.contact-head{font-family:'Audiowide',sans-serif;color:var(--white);font-size:17.5px;left:0;right:0;top:525px;text-align:center}
.contact-sub{left:68px;right:68px;top:545px;text-align:center;color:#fff3e4;font-size:10.2px;line-height:12.5px}
.contact-line{left:0;right:0;top:580px;display:flex;justify-content:center;align-items:center;gap:10px;color:var(--white);font-size:16.5px}
.contact-line .sep{width:1px;height:18px;background:var(--white);margin:0 2px}
.contact-item{display:flex;align-items:center;gap:5px}
.hours-label{font-family:'Audiowide',sans-serif;color:var(--orange);font-size:15px;left:0;right:0;top:647px;text-align:center}
.hours-box{left:44px;width:434px;top:657px;height:35px;border:2px solid var(--tan);border-radius:4px;display:flex;align-items:center;justify-content:center;font-family:'Audiowide',sans-serif;color:var(--white);font-size:15.5px}
.hours-label span{background:var(--dark);padding:0 6px;position:relative;z-index:2}
.delivery{left:0;right:0;top:700px;text-align:center;font-family:'Audiowide',sans-serif;font-size:13px;color:var(--white)}
.delivery b{color:var(--orange);font-weight:400}
</style>
</head>
<body>

<section class="page page--front">
  <svg class="layer" viewBox="0 0 522 741">
    <defs>
      <linearGradient id="shelf" x1="0" y1="0" x2="0" y2="1"><stop offset="0" stop-color="#3a2c22"/><stop offset="1" stop-color="#241d18"/></linearGradient>
      <linearGradient id="ribbon" x1="0" y1="0" x2="1" y2="0"><stop offset="0" stop-color="#e47a24"/><stop offset=".5" stop-color="#ee8a2c"/><stop offset="1" stop-color="#e57c25"/></linearGradient>
      <linearGradient id="loafA" x1="0" y1="0" x2="1" y2="1"><stop offset="0" stop-color="#c9955c"/><stop offset="1" stop-color="#6d4322"/></linearGradient>
      <linearGradient id="loafB" x1="0" y1="0" x2="1" y2="1"><stop offset="0" stop-color="#3a2a1f"/><stop offset="1" stop-color="#a9673a"/></linearGradient>
      <linearGradient id="loafC" x1="0" y1="0" x2="1" y2="1"><stop offset="0" stop-color="#5a3b26"/><stop offset="1" stop-color="#b7824f"/></linearGradient>
    </defs>
    <rect x="0" y="0" width="522" height="260" fill="url(#shelf)" role="img" aria-label="Foto: Brote in einem dunklen Bäckereiregal"/>
    <circle class="brand-mark" cx="261" cy="76" r="42" fill="var(--orange)"/>
    <polygon points="0,158 522,222 522,262 0,262" fill="var(--peach)"/>
    <polygon points="0,198 522,262 522,500 0,500" fill="var(--white)"/>
    <polygon points="0,158 90,169 0,198" fill="var(--peach)"/>
    <polygon points="380,215 522,232 522,262 480,262" fill="var(--peach)"/>
    <polygon points="40,176 508,176 449,259 483,318 13,318 75,246" fill="url(#ribbon)"/>
    <g opacity=".35">
      <ellipse cx="42" cy="362" rx="26" ry="17" fill="var(--peach)" role="img" aria-label="Zeichnung eines Croissants"/>
      <circle cx="492" cy="370" r="38" fill="var(--peach)" role="img" aria-label="Zeichnung eines Brötchens"/>
      <circle cx="14" cy="430" r="34" fill="var(--peach)" role="img" aria-label="Zeichnung einer Brezel"/>
    </g>
    <g stroke="var(--orange)" stroke-width="2" fill="none">
      <line x1="66" y1="447" x2="100" y2="447"/><line x1="124" y1="447" x2="170" y2="447"/>
      <circle cx="112" cy="447" r="7"/><polyline points="108,447 111,450 117,442"/>
      <line x1="240" y1="447" x2="324" y2="447"/><line x1="348" y1="447" x2="440" y2="447"/>
      <circle cx="336" cy="447" r="7"/><polyline points="332,447 335,450 341,442"/>
    </g>
    <polygon points="0,499 182,499 152,700 0,700" fill="url(#loafA)" role="img" aria-label="Foto: angeschnittenes Bauernbrot"/>
    <polygon points="187,499 362,499 334,668 151,700" fill="url(#loafB)" role="img" aria-label="Foto: Brötchen im Korb mit Ähren"/>
    <polygon points="367,499 522,499 522,632 338,668" fill="url(#loafC)" role="img" aria-label="Foto: rustikale Brotlaibe"/>
    <polygon points="0,700 522,632 522,741 0,741" fill="var(--dark)"/>
    <polygon points="330,675 522,632 522,665" fill="var(--tan)"/>
    <polygon points="380,741 500,650 512,660 400,741" fill="#ffffff" opacity=".12" role="img" aria-label="Zeichnung eines Baguettes"/>
  </svg>
  <div class="abs brand-name">TEIGWICHTELHOF</div>
  <div class="abs ribbon-kicker">Unsere Backwaren einmalig</div>
  <div class="abs ribbon-main">kostenlos</div>
  <div class="abs ribbon-sub">auszuprobieren.</div>
  <p class="abs intro-head">Teigwichtelhof bietet den Service für Frühstücksfreunde, Langschläfer und Wochenend-Genießer!</p>
  <p class="abs intro-body">Wir sind der Lieferservice für frische Backwaren in Bremen und Umgebung. Gemeinsam mit unserer Partnerbäckerei arbeiten wir Hand in Hand an der Zufriedenheit unserer Kunden und liefern unsere Vielfalt täglich direkt an die Haustür. Die von uns angebotenen Waren werden mit ausgewählten Zutaten hergestellt und liebevoll von Hand veredelt.</p>
  <div class="usp usp--one">Ofenfrisch geliefert!</div>
  <div class="usp usp--two">Kostenlos und unverbindlich probieren</div>
  <div class="abs url" style="left:0;width:522px;top:693px;padding-right:50px">www.teigwichtelhof.de</div>
</section>

<section class="page page--back">
  <svg class="layer" viewBox="0 0 522 741">
    <defs>
      <linearGradient id="bakeA" x1="0" y1="0" x2="1" y2="1"><stop offset="0" stop-color="#e6a862"/><stop offset="1" stop-color="#8a4d22"/></linearGradient>
      <linearGradient id="bakeB" x1="0" y1="0" x2="0" y2="1"><stop offset="0" stop-color="#c7652a"/><stop offset="1" stop-color="#d99a52"/></linearGradient>
      <linearGradient id="band" x1="0" y1="0" x2="1" y2="1"><stop offset="0" stop-color="#e8822a"/><stop offset="1" stop-color="#f0a034"/></linearGradient>
    </defs>
    <rect x="0" y="0" width="522" height="506" fill="#2f2824" role="img" aria-label="Foto: dunkle Brotauslage im Hintergrund"/>
    <polygon points="0,0 522,0 522,50 0,128" fill="var(--white)"/>
    <rect x="0" y="0" width="522" height="18" fill="#f6eadb" opacity=".6" role="img" aria-label="Gezeichnete Backwaren als Bordüre"/>
    <rect x="22" y="20" width="480" height="167" rx="14" fill="var(--white)"/>
    <rect x="271" y="28" width="220" height="152" rx="12" fill="url(#bakeA)" role="img" aria-label="Foto: Zimtschnecke, Croissants und Brötchen"/>
    <rect x="22" y="196" width="480" height="168" rx="14" fill="var(--white)"/>
    <rect x="32" y="203" width="219" height="153" rx="12" fill="url(#bakeB)" role="img" aria-label="Foto: Brote in einer beleuchteten Auslage"/>
    <polygon points="0,364 166,364 150,506 0,506" fill="#b88a56" role="img" aria-label="Foto: angeschnittenes Bauernbrot"/>
    <polygon points="170,364 345,364 330,506 154,506" fill="#7a4a27" role="img" aria-label="Foto: Brötchen im Korb mit Ähren"/>
    <polygon points="349,364 522,364 522,506 334,506" fill="#6a4529" role="img" aria-label="Foto: rustikale Brotlaibe"/>
    <polygon points="138,473 396,473 380,490 396,506 122,506" fill="var(--darker)"/>
    <rect x="0" y="506" width="522" height="117" fill="url(#band)"/>
    <rect x="0" y="623" width="522" height="5" fill="var(--white)"/>
    <rect x="0" y="628" width="522" height="113" fill="var(--dark)"/>
  </svg>

  <h2 class="abs card-title" style="left:37px;top:36px">GUTEN MORGEN,<br>FRÜHSTÜCK IST DA!</h2>
  <p class="abs card-text" style="left:37px;width:218px;top:73px">Frische Backwaren zum Frühstück, wann Immer du es wünschst – Teigwichtelhof bringt sie Dir frühmorgens direkt an die Haustür. Woche für Woche. An einem oder mehreren Tagen, werktags und auch am Wochenende. Spare Dir den Weg zum Bäcker und gewinne wertvolle Zeit am frühen Morgen.</p>

  <h2 class="abs card-title" style="left:268px;top:215px;font-size:15.5px;line-height:19px">EINFACH,<br>SCHNELL &amp; FRISCH</h2>
  <p class="abs card-text card-text--small" style="left:268px;width:220px;top:256px">Wir sind mehr als nur ein Brötchenlieferservice, denn die Zufriedenheit und Bequemlichkeit unserer Kunden liegt uns sehr am Herzen. Daher haben wir es uns zur Aufgabe gemacht, Dir ein unkompliziertes und vor allem leckeres Frühstück zu liefern. Die ofenfrischen Backwaren und ausgewählte Zutaten sorgen für einen unvergesslichen Geschmack</p>

  <div class="abs url" style="left:130px;width:266px;top:477px;font-size:16.5px">www.teigwichtelhof.de</div>

  <h3 class="abs contact-head">NEHMEN SIE KONTAKT MIT UNS AUF</h3>
  <p class="abs contact-sub">Hinterlassen Sie uns eine Nachricht zu Ihrem Anliegen, wir melden uns schnellstmöglich bei Ihnen zurück und haben sicherlich die richtigen Antworten!</p>
  <div class="abs contact-line">
    <span class="contact-item">
      <svg width="14" height="14" viewBox="0 0 14 14"><circle cx="7" cy="7" r="7" fill="#fff"/><path d="M4.3 3.6l1.4-.3.8 1.9-.9.7c.4 1 1.2 1.8 2.2 2.3l.7-.9 1.9.8-.3 1.4c-3.3 0-5.8-2.6-5.8-5.9z" fill="var(--orange)"/></svg>
      04203-5519370
    </span>
    <span class="sep"></span>
    <span class="contact-item">
      <svg width="14" height="14" viewBox="0 0 14 14"><circle cx="7" cy="7" r="7" fill="#fff"/><rect x="3.5" y="4.5" width="7" height="5" fill="none" stroke="var(--orange)" stroke-width="1"/><polyline points="3.5,4.5 7,7.5 10.5,4.5" fill="none" stroke="var(--orange)" stroke-width="1"/></svg>
      kunden@teigwichtelhof.de
    </span>
  </div>

  <div class="abs hours-box">Montag-Freitag: 09-12 Uhr - 14-16 Uhr</div>
  <div class="abs hours-label"><span>Bürozeit</span></div>
  <div class="abs delivery"><b>Liefertage:</b> Montags-Sonntags</div>
</section>

</body>
</html>
```